Business Card Design

We need a design for business cards for our company. We have a logo. We teach EMT's and we are based out of Virginia. The information that will need to add would be, name, title, phone number, email, address. On the back of the business card would be "We help you, help others"

Target Market(s)

People that want to become EMT's

Colors

Designer to choose colors to be used in the design.

Requirements
Must have
• company logo

```html
<!DOCTYPE html>
<html lang="en">
<head>
<meta charset="utf-8">
<title>Rescue Ready Academy – Business Cards</title>
<link rel="stylesheet" href="https://fonts.googleapis.com/css2?family=Work+Sans:wght@400;500;600&display=swap">
<style>
  :root {
    --backdrop: #0d0d0d;
    --card: #1d1d1e;
    --card-edge: #2a2a2b;
    --silver: #c8c8ca;
    --silver-soft: #a9a9ab;
    --rule: #8d8d90;
  }
  * { margin: 0; padding: 0; box-sizing: border-box; }
  html, body {
    width: 1200px; height: 900px; overflow: hidden;
    background: var(--backdrop);
    font-family: "Work Sans", Arial, sans-serif;
    color: var(--silver);
  }
  .canvas {
    position: relative; width: 1200px; height: 900px;
    background: radial-gradient(ellipse at 50% 40%, #1a1a1a 0%, var(--backdrop) 70%);
  }
  .card {
    position: absolute; left: 260px; width: 680px; height: 388px;
    background: linear-gradient(135deg, var(--card) 0%, #222223 60%, #1a1a1b 100%);
    border: 1px solid var(--card-edge);
    box-shadow: 0 18px 40px rgba(0,0,0,0.6);
  }
  .card--front { top: 40px; }
  .card--back { top: 472px; }

  .brand { display: flex; align-items: center; gap: 14px; }
  .brand__dot {
    width: 22px; height: 22px; border-radius: 50%;
    background: var(--silver); flex: none;
  }
  .brand__name {
    font-weight: 600; font-size: 32px; letter-spacing: 0.5px;
    line-height: 1.1; color: var(--silver); white-space: nowrap;
  }

  .front-lockup {
    position: absolute; inset: 0;
    display: flex; flex-direction: column;
    align-items: center; justify-content: center; gap: 22px;
  }
  .slogan {
    font-size: 16px; font-weight: 400; letter-spacing: 3px;
    text-transform: uppercase; color: var(--silver-soft);
    white-space: nowrap;
  }

  .card--back .brand {
    position: absolute; left: 46px; top: 50%;
    transform: translateY(-50%);
  }
  .card--back .brand__name { font-size: 27px; }
  .divider {
    position: absolute; left: 345px; top: 66px;
    width: 1px; height: 256px; background: var(--rule);
  }
  .contact { position: absolute; left: 382px; top: 74px; }
  .contact__name {
    font-weight: 500; font-size: 29px; letter-spacing: 1.5px;
    text-transform: uppercase; color: var(--silver);
  }
  .contact__title { font-size: 17px; color: var(--silver-soft); margin-bottom: 20px; }
  .contact__address { font-size: 18px; line-height: 1.4; margin-bottom: 12px; }
  .contact__row { display: flex; align-items: center; gap: 10px; font-size: 19px; line-height: 1.6; }
  .contact__icon { width: 14px; height: 14px; flex: none; }
</style>
</head>
<body>
<main class="canvas">
  <section class="card card--front" aria-label="Card front">
    <div class="front-lockup">
      <div class="brand">
        <span class="brand__dot"></span>
        <span class="brand__name">Rescue Ready Academy</span>
      </div>
      <p class="slogan">We help you, help others</p>
    </div>
  </section>

  <section class="card card--back" aria-label="Card back">
    <div class="brand">
      <span class="brand__dot"></span>
      <span class="brand__name">Rescue Ready<br>Academy</span>
    </div>
    <div class="divider"></div>
    <div class="contact">
      <p class="contact__name">Daniel Reyes</p>
      <p class="contact__title">Director</p>
      <p class="contact__address">418 Harbor St.<br>Lakeview, VA 23301</p>
      <p class="contact__row">
        <svg class="contact__icon" viewBox="0 0 16 16" fill="none" stroke="currentColor" stroke-width="1.5"><path d="M4 1.5 6 4.5 4.8 6a8 8 0 0 0 5.2 5.2L11.5 10l3 2-1.3 2.5C7 14 2 9 1.5 2.8Z"/></svg>
        555-204-7731
      </p>
      <p class="contact__row">
        <svg class="contact__icon" viewBox="0 0 16 16" fill="none" stroke="currentColor" stroke-width="1.5"><rect x="1.5" y="3.5" width="13" height="9"/><path d="M1.5 3.5 8 9l6.5-5.5"/></svg>
        info@rescueready.com
      </p>
      <p class="contact__row">
        <svg class="contact__icon" viewBox="0 0 16 16" fill="none" stroke="currentColor" stroke-width="1.3"><circle cx="8" cy="8" r="6.5"/><ellipse cx="8" cy="8" rx="3" ry="6.5"/><path d="M1.5 8h13"/></svg>
        www.rescueready.com
      </p>
    </div>
  </section>
</main>
</body>
</html>
```